LHP Regal Business Card Design 2020

Your Manor Steward is looking for a business card that is clean and straight to the point but still looks high-end and attractive. We are a team comprised of management and field professionals focused on the high-end residential marketplace. We serve homeowners and trade professionals directly based out of the Metrowest/Boston area. We provide client services as well as construction/renovation services.
We are aiming for a black and white feel (white background and black text) and a matte finish with rounded edges.

We want to emphasis our vision of "Properties - Projects - Partners".
Dana Pellham is the president of LHP

Please include the following areas we service: Boston/Cape/Newport
Please make sure to include Dana's mobile (555) 213 4480 & office number (555) 640 1937, email dana@yourmanorsteward.example and website www.yourmanorsteward.example

Colors

Designer to choose only greyscale colors for use in the design.

Requirements
Must have
• Include "Properties - Projects - Partners" in design

Include "After Hours Emergency Support # 1800 555 0142" with icon

```html
<!DOCTYPE html>
<html lang="en">
<head>
<meta charset="utf-8">
<title>LHP Business Card</title>
<link rel="stylesheet" href="https://fonts.googleapis.com/css2?family=Source+Sans+3:wght@400;600;700;800&display=swap">
<style>
  :root {
    --bg: #e2e2e2;
    --card: #f4f4f4;
    --ink: #231f20;
    --rule: #555555;
    --shadow: rgba(0,0,0,0.35);
  }
  html, body {
    margin: 0;
    width: 1200px;
    height: 960px;
    overflow: hidden;
    background: var(--bg);
    font-family: "Source Sans 3", "Helvetica Neue", Arial, sans-serif;
    color: var(--ink);
  }
  p, h1, h2, ul { margin: 0; }
  .stage { position: relative; width: 1200px; height: 960px; }
  .card {
    position: absolute;
    left: 312px;
    width: 581px;
    height: 333px;
    background: var(--card);
    box-shadow: 2px 3px 5px var(--shadow);
  }
  .card--front { top: 127px; }
  .card--back { top: 511px; height: 332px; }

  .brand-name {
    position: absolute;
    font-weight: 800;
    line-height: 1;
    letter-spacing: -2px;
    color: var(--ink);
  }
  .card--front .brand-name {
    left: 0; right: 0;
    top: 92px;
    text-align: center;
    font-size: 150px;
  }
  .vision {
    position: absolute;
    left: 38px; right: 38px;
    top: 286px;
    display: flex;
    align-items: center;
    gap: 6px;
    font-size: 15px;
    line-height: 20px;
    letter-spacing: 1.3px;
    white-space: nowrap;
  }
  .vision::before, .vision::after {
    content: "";
    flex: 1;
    height: 1px;
    background: var(--rule);
  }

  .card--back .brand-name {
    right: 35px;
    top: 30px;
    font-size: 80px;
  }
  .brand-sub {
    position: absolute;
    right: 41px;
    top: 113px;
    font-size: 11px;
    font-weight: 700;
    letter-spacing: 1.2px;
  }
  .person {
    position: absolute;
    left: 41px;
    right: 35px;
    top: 138px;
  }
  .person__name {
    font-size: 19px;
    font-weight: 700;
    line-height: 24px;
  }
  .person__role {
    display: flex;
    align-items: center;
    gap: 6px;
    font-size: 15px;
    line-height: 18px;
  }
  .person__role::after {
    content: "";
    flex: 1;
    height: 1px;
    background: var(--ink);
    margin-top: 6px;
  }
  .contacts {
    position: absolute;
    left: 41px;
    top: 194px;
    padding: 0;
    list-style: none;
    font-size: 15px;
    line-height: 19px;
  }
  .contacts li { display: flex; align-items: center; gap: 4px; white-space: nowrap; }
  .contacts svg { width: 13px; height: 13px; flex: none; }
  .contacts .emergency { font-weight: 600; }
  .areas {
    position: absolute;
    left: 41px;
    top: 297px;
    font-size: 15px;
    line-height: 19px;
  }
</style>
</head>
<body>
<div class="stage">
  <section class="card card--front">
    <h1 class="brand-name">LHP</h1>
    <p class="vision">PROPERTIES - PROJECTS - PARTNERS</p>
  </section>

  <section class="card card--back">
    <h2 class="brand-name">LHP</h2>
    <p class="brand-sub">YOUR MANOR STEWARD</p>
    <div class="person">
      <p class="person__name">Dana Pellham</p>
      <p class="person__role">President</p>
    </div>
    <ul class="contacts">
      <li>
        <svg viewBox="0 0 13 13" aria-hidden="true"><rect x="3" y="0.5" width="7" height="12" rx="1" fill="none" stroke="#231f20" stroke-width="1.2"/><rect x="4.3" y="2" width="4.4" height="7.5" fill="#231f20"/></svg>
        (555) 213 4480
      </li>
      <li>
        <svg viewBox="0 0 13 13" aria-hidden="true"><path d="M2.5 1 L5 1 L6 4 L4.5 5.2 C5.3 7 6 7.7 7.8 8.5 L9 7 L12 8 L12 10.5 C12 11.5 11 12.2 10 12 C5.5 11 2 7.5 1 3 C0.8 2 1.5 1 2.5 1 Z" fill="#231f20"/></svg>
        (555) 640 1937
      </li>
      <li>
        <svg viewBox="0 0 13 13" aria-hidden="true"><rect x="0.8" y="2.5" width="11.4" height="8" fill="none" stroke="#231f20" stroke-width="1.2"/><path d="M0.8 2.5 L6.5 7 L12.2 2.5" fill="none" stroke="#231f20" stroke-width="1.2"/></svg>
        dana@yourmanorsteward.example
      </li>
      <li>
        <svg viewBox="0 0 13 13" aria-hidden="true"><circle cx="6.5" cy="6.5" r="5.7" fill="none" stroke="#231f20" stroke-width="1.1"/><ellipse cx="6.5" cy="6.5" rx="2.5" ry="5.7" fill="none" stroke="#231f20" stroke-width="1"/><path d="M0.8 6.5 H12.2 M1.8 3.6 H11.2 M1.8 9.4 H11.2" stroke="#231f20" stroke-width="0.9"/></svg>
        www.yourmanorsteward.example
      </li>
      <li class="emergency">
        <svg viewBox="0 0 13 13" aria-hidden="true"><circle cx="6.5" cy="6.5" r="5.7" fill="none" stroke="#231f20" stroke-width="1.2"/><path d="M6.5 3 V6.8 L9 8.3" fill="none" stroke="#231f20" stroke-width="1.2" stroke-linecap="round"/></svg>
        After Hours Emergency Support # 1800 555 0142
      </li>
    </ul>
    <p class="areas">Boston | Metrowest | South Shore | Cape | Newport</p>
  </section>
</div>
</body>
</html>
```